Clear Coat 5L & 2.5L kit

Clear coat 5 Liter with 2.5 Liter hardener
I attached few examples
Required size:
5L
Actual size is: 22.875 x 10.4375 inch
With bleed added: 23.125 x 10.6875 inch
2.5L
Actual size is: 22.875 x 6.1875 inch
With bleed added: 23.125x6.2125 inch

Thanks

```html
<!DOCTYPE html>
<html lang="en">
<head>
<meta charset="utf-8">
<title>Valence Coatings – Apex Hardener 2.5L Labels</title>
<link rel="stylesheet" href="https://fonts.googleapis.com/css2?family=Montserrat:wght@500;600;700;800&family=Roboto+Condensed:wght@400;700&display=swap">
<style>
:root{
  --page-top:#f3f6f8;
  --page-bottom:#d3dfe6;
  --navy-deep:#0a0f17;
  --navy:#0e1a2a;
  --navy-mid:#132a3d;
  --panel:#0b0c0f;
  --teal:#5ed1b8;
  --teal-soft:rgba(94,209,184,.35);
  --yellow:#f5c400;
  --white:#ffffff;
  --grey:#cfd5db;
  --hazard:#c8102e;
}
*{box-sizing:border-box;margin:0;padding:0}
html,body{width:1200px;height:1038px;overflow:hidden}
body{background:linear-gradient(180deg,var(--page-top),var(--page-bottom));position:relative;font-family:"Roboto Condensed",Arial,sans-serif;color:var(--white)}

.label{position:absolute;left:46px;width:1115px;height:303px;overflow:hidden;
  background:linear-gradient(90deg,var(--navy-deep) 0%,var(--navy) 45%,var(--navy-deep) 100%)}
.label--fast{top:27px}.label--slow{top:360px}.label--medium{top:697px}
.label__texture{position:absolute;inset:0;
  background:
   radial-gradient(ellipse 240px 120px at 90px 250px,var(--teal-soft),transparent 70%),
   radial-gradient(ellipse 200px 140px at 560px 210px,rgba(94,209,184,.22),transparent 70%),
   radial-gradient(ellipse 160px 120px at 720px 150px,rgba(94,209,184,.18),transparent 70%),
   radial-gradient(ellipse 180px 90px at 1060px 290px,rgba(94,209,184,.2),transparent 70%)}
.label__spine{position:absolute;left:26px;top:188px;transform:rotate(-90deg);transform-origin:0 0;
  font-family:"Montserrat",sans-serif;font-size:15px;letter-spacing:.5px;white-space:nowrap}
.label__spine .thin{color:var(--teal);font-weight:500}
.label__spine .bold{font-weight:700}

/* front panel */
.front{position:absolute;left:232px;top:26px;width:219px;height:277px;background:var(--panel);overflow:hidden}
.front__texture{position:absolute;left:0;right:0;top:108px;bottom:0;
  background:linear-gradient(180deg,var(--panel),var(--navy-mid) 60%,#10263a)}
.brand{font-family:"Montserrat",sans-serif;font-weight:800;color:var(--white);line-height:1;white-space:nowrap}
.front .brand{position:absolute;left:35px}
.front .brand--name{top:21px;font-size:30px;letter-spacing:-.5px}
.front .brand--sub{top:68px;font-size:15.5px;letter-spacing:3.3px}
.product{position:absolute;left:35px;top:118px;width:151px;font-family:"Montserrat",sans-serif}
.product__line{font-size:12px;font-weight:500;color:var(--teal);letter-spacing:.5px;line-height:14px}
.product__title{font-size:13.4px;font-weight:600;letter-spacing:1.2px;line-height:17px;margin-top:2px;white-space:nowrap}
.product__meta{display:flex;justify-content:space-between;font-family:"Roboto Condensed",sans-serif;font-size:9.5px;line-height:11px;margin-top:1px}
.product__speed{color:var(--yellow);letter-spacing:1px}
.front__size{position:absolute;left:35px;top:240px;font-family:"Montserrat",sans-serif;font-weight:700;font-size:20px;color:var(--yellow)}
.front__mix{position:absolute;left:146px;top:248px;font-family:"Montserrat",sans-serif;font-weight:600;font-size:11px}

/* side info panel */
.info{position:absolute;left:544px;top:26px;width:121px;height:277px;background:var(--panel);padding:9px 7px;font-size:4.6px;line-height:1.32;color:var(--grey)}
.info .brand--name{font-size:16.5px;letter-spacing:-.3px}
.info .brand--sub{font-size:8.6px;letter-spacing:1.6px;margin-top:2px;margin-bottom:19px}
.info p{margin-bottom:4px;width:108px}
.info b{color:var(--white)}
.info .caps{text-transform:uppercase;font-weight:700;color:var(--white)}
.info .caps--plain{font-weight:400}
.info__address{position:absolute;left:7px;top:208px;font-size:5.6px;line-height:1.35;color:var(--white)}
.info__origin{position:absolute;left:7px;top:252px;font-size:5.6px;color:var(--white)}
.info__liters{position:absolute;left:108px;top:268px;transform:rotate(-90deg);transform-origin:0 0;
  font-family:"Montserrat",sans-serif;font-weight:700;font-size:9px;color:var(--yellow);white-space:nowrap}

/* back panel */
.back{position:absolute;left:751px;top:0;width:238px;height:303px;background:var(--panel);padding:29px 8px 0 8px;font-size:4.3px;line-height:5.1px;color:var(--grey)}
.back p{margin-bottom:2.5px}
.back b{color:var(--white)}
.speed-table{float:right;width:46px;margin:0 -4px 3px 6px;border:.5px solid #888;font-size:3.8px;line-height:4.4px;border-collapse:collapse}
.speed-table td{padding:.3px 1.5px;border-bottom:.5px solid #555}
.speed-table td:last-child{text-align:right}
.back__keep{font-size:6px;line-height:7px;font-weight:700;color:var(--white);margin-top:3px}
.back__contents{width:160px}
.danger{position:absolute;right:10px;top:262px;width:48px;text-align:center;border:.6px solid #aaa;background:var(--white);padding-bottom:2px}
.danger__word{display:block;background:var(--panel);color:var(--white);font-weight:700;font-size:6.5px;line-height:8px;letter-spacing:.5px}
.danger svg{display:block;margin:1px auto 0}
</style>
</head>
<body>

<!-- ===== FAST ===== -->
<section class="label label--fast">
  <div class="label__texture" role="img" aria-label="Teal dotted wave texture across the navy background"></div>
  <div class="label__spine"><span class="thin">APEX </span><span class="bold">HARDENER</span></div>
  <div class="front">
    <div class="front__texture" role="img" aria-label="Dotted wave texture in deep navy"></div>
    <div class="brand brand--name">VALENCE</div>
    <div class="brand brand--sub">COATINGS</div>
    <div class="product">
      <div class="product__line">APEX</div>
      <div class="product__title">HARDENER<br>FOR CLEAR COAT</div>
      <div class="product__meta"><span>VOC 2.1</span><span class="product__speed">Fast 341</span></div>
    </div>
    <div class="front__size">2.5L</div>
    <div class="front__mix">2:1 MIX</div>
  </div>
  <div class="info">
    <div class="brand brand--name">VALENCE</div>
    <div class="brand brand--sub">COATINGS</div>
    <p class="caps caps--plain">For sale only by professionals.<br>Not for sale to or use by general public</p>
    <p><b>Notice to purchaser:</b> Limited warranty. Seller warrants this product to be free of defects in material and workmanship. Buyer is responsible for determining the suitability of the product for the intended use and assumes all risk and liability in connection with its use.</p>
    <p class="caps">Warning: flammable liquid and vapor. Vapor and spray mist harmful if inhaled. May cause central nervous system effects such as dizziness, headache or nausea. May cause nose, throat, eye and skin irritation. (Follow all directions and cautions on back panel)</p>
    <p><b>Warranty:</b> Recommendations for application are based on tests believed to be reliable. Since conditions of use are beyond our control, no warranty is expressed or implied beyond replacement of product proven defective. Intended for use by professional personnel only.</p>
    <div class="info__address">Valence Coatings, Inc.<br>420 Harbor Park Way,<br>Riverside, CA 92501<br>(888) 555-0147</div>
    <div class="info__origin">Made in EU</div>
    <div class="info__liters">2.5 LITERS</div>
  </div>
  <div class="back">
    <table class="speed-table"><tr><td>Speed</td><td>Temperature</td></tr><tr><td>Slow</td><td>80°F–100°F</td></tr><tr><td>Medium</td><td>65°F–80°F</td></tr><tr><td>Fast</td><td>50°F–65°F</td></tr></table>
    <p><b>Description:</b> Hardener for use with Apex clear coat. Hardener is available in three speeds. Please choose the appropriate speed according to the working temperature.</p>
    <p><b>DIRECTIONS:</b><br>1. Read all label directions, warnings and cautions on panel and hardener.<br>2. Mixing: 2 parts clear coat with 1 part hardener by volume. Stir well.<br>3. Adjust air pressure to 25–30 psi at the gun cap, or 10 psi at the cap for HVLP guns.<br>4. Apply 2 full wet coats, allowing 5–10 minutes flash time between coats for best flow and gloss.<br>5. Dust free in 15 minutes, tack free in 40 minutes at 70°F. May be force dried 30 minutes at 140°F metal temperature after a 10 minute flash.<br>6. Accelerator: up to 1 oz per mixed quart may be added to speed drying in cool conditions. Do not exceed the stated amount or pot life will be shortened.<br>7. Wet sand with 1500 grit or finer and polish after 24 hours air dry or after cool down from bake.<br>8. Clean spray equipment immediately after use with lacquer thinner or gun wash.</p>
    <p><b>WARNING: FLAMMABLE LIQUID AND VAPOR. VAPOR AND SPRAY MIST HARMFUL. MAY CAUSE LUNG IRRITATION AND ALLERGIC RESPIRATORY REACTION.</b> Keep away from heat, sparks and open flame. Vapors may cause flash fire. Persons with asthma or other breathing problems should not use or be exposed to this product. Do not breathe vapors or spray mist. Use only with adequate ventilation. Wear a properly fitted supplied air respirator or an approved organic vapor cartridge respirator during and after application until vapors are gone. Avoid contact with eyes, skin and clothing. Wear chemical resistant gloves and safety glasses. Keep container tightly closed when not in use. Do not reseal if contamination with water is suspected, as pressure may build. Dispose of empty containers and waste according to federal, state and local regulations. Read the Safety Data Sheet before use.</p>
    <p><b>FIRST AID:</b> If inhaled, remove to fresh air and restore breathing if needed; get medical attention. In case of skin contact, wash thoroughly with soap and water and remove contaminated clothing. In case of eye contact, flush with plenty of water for at least 15 minutes and get medical attention. If swallowed, do not induce vomiting; call a physician immediately.</p>
    <p><b>NOTICE:</b> Reports have associated repeated and prolonged occupational overexposure to solvents with permanent brain and nervous system damage. Intentional misuse by deliberately concentrating and inhaling the contents may be harmful or fatal.</p>
    <p><b>California Notice: WARNING!</b> This product contains chemicals known to the State of California to cause cancer, birth defects or other reproductive harm.</p>
    <div class="back__keep">KEEP OUT OF THE REACH OF CHILDREN</div>
    <p><b>For professional use only by trained and qualified paint personnel using all proper safety equipment and application techniques.</b></p>
    <p class="back__contents"><b>Contents:</b> Hexamethylene diisocyanate polymer, butyl acetate, xylene, ethylbenzene, methyl amyl ketone. <b>EMERGENCY TELEPHONE: 1-800-555-0142.</b> Spray rate: 2:1 mix VOC.</p>
    <div class="danger"><span class="danger__word">DANGER</span>
      <svg width="44" height="14" viewBox="0 0 44 14" aria-hidden="true"><g fill="none" stroke="var(--hazard)" stroke-width="1.2"><path d="M7 1l6 6-6 6-6-6z"/><path d="M22 1l6 6-6 6-6-6z"/><path d="M37 1l6 6-6 6-6-6z"/></g><g fill="#111"><circle cx="7" cy="7.5" r="2"/><circle cx="22" cy="7.5" r="2"/><circle cx="37" cy="7.5" r="2"/></g></svg>
    </div>
  </div>
</section>

<!-- ===== SLOW ===== -->
<section class="label label--slow">
  <div class="label__texture" role="img" aria-label="Teal dotted wave texture across the navy background"></div>
  <div class="label__spine"><span class="thin">APEX </span><span class="bold">HARDENER</span></div>
  <div class="front">
    <div class="front__texture" role="img" aria-label="Dotted wave texture in deep navy"></div>
    <div class="brand brand--name">VALENCE</div>
    <div class="brand brand--sub">COATINGS</div>
    <div class="product">
      <div class="product__line">APEX</div>
      <div class="product__title">HARDENER<br>FOR CLEAR COAT</div>
      <div class="product__meta"><span>VOC 2.1</span><span class="product__speed">Slow 345</span></div>
    </div>
    <div class="front__size">2.5L</div>
    <div class="front__mix">2:1 MIX</div>
  </div>
  <div class="info">
    <div class="brand brand--name">VALENCE</div>
    <div class="brand brand--sub">COATINGS</div>
    <p class="caps caps--plain">For sale only by professionals.<br>Not for sale to or use by general public</p>
    <p><b>Notice to purchaser:</b> Limited warranty. Seller warrants this product to be free of defects in material and workmanship. Buyer is responsible for determining the suitability of the product for the intended use and assumes all risk and liability in connection with its use.</p>
    <p class="caps">Warning: flammable liquid and vapor. Vapor and spray mist harmful if inhaled. May cause central nervous system effects such as dizziness, headache or nausea. May cause nose, throat, eye and skin irritation. (Follow all directions and cautions on back panel)</p>
    <p><b>Warranty:</b> Recommendations for application are based on tests believed to be reliable. Since conditions of use are beyond our control, no warranty is expressed or implied beyond replacement of product proven defective. Intended for use by professional personnel only.</p>
    <div class="info__address">Valence Coatings, Inc.<br>420 Harbor Park Way,<br>Riverside, CA 92501<br>(888) 555-0147</div>
    <div class="info__origin">Made in EU</div>
    <div class="info__liters">2.5 LITERS</div>
  </div>
  <div class="back">
    <table class="speed-table"><tr><td>Speed</td><td>Temperature</td></tr><tr><td>Slow</td><td>80°F–100°F</td></tr><tr><td>Medium</td><td>65°F–80°F</td></tr><tr><td>Fast</td><td>50°F–65°F</td></tr></table>
    <p><b>Description:</b> Hardener for use with Apex clear coat. Hardener is available in three speeds. Please choose the appropriate speed according to the working temperature.</p>
    <p><b>DIRECTIONS:</b><br>1. Read all label directions, warnings and cautions on panel and hardener.<br>2. Mixing: 2 parts clear coat with 1 part hardener by volume. Stir well.<br>3. Adjust air pressure to 25–30 psi at the gun cap, or 10 psi at the cap for HVLP guns.<br>4. Apply 2 full wet coats, allowing 5–10 minutes flash time between coats for best flow and gloss.<br>5. Dust free in 15 minutes, tack free in 40 minutes at 70°F. May be force dried 30 minutes at 140°F metal temperature after a 10 minute flash.<br>6. Accelerator: up to 1 oz per mixed quart may be added to speed drying in cool conditions. Do not exceed the stated amount or pot life will be shortened.<br>7. Wet sand with 1500 grit or finer and polish after 24 hours air dry or after cool down from bake.<br>8. Clean spray equipment immediately after use with lacquer thinner or gun wash.</p>
    <p><b>WARNING: FLAMMABLE LIQUID AND VAPOR. VAPOR AND SPRAY MIST HARMFUL. MAY CAUSE LUNG IRRITATION AND ALLERGIC RESPIRATORY REACTION.</b> Keep away from heat, sparks and open flame. Vapors may cause flash fire. Persons with asthma or other breathing problems should not use or be exposed to this product. Do not breathe vapors or spray mist. Use only with adequate ventilation. Wear a properly fitted supplied air respirator or an approved organic vapor cartridge respirator during and after application until vapors are gone. Avoid contact with eyes, skin and clothing. Wear chemical resistant gloves and safety glasses. Keep container tightly closed when not in use. Do not reseal if contamination with water is suspected, as pressure may build. Dispose of empty containers and waste according to federal, state and local regulations. Read the Safety Data Sheet before use.</p>
    <p><b>FIRST AID:</b> If inhaled, remove to fresh air and restore breathing if needed; get medical attention. In case of skin contact, wash thoroughly with soap and water and remove contaminated clothing. In case of eye contact, flush with plenty of water for at least 15 minutes and get medical attention. If swallowed, do not induce vomiting; call a physician immediately.</p>
    <p><b>NOTICE:</b> Reports have associated repeated and prolonged occupational overexposure to solvents with permanent brain and nervous system damage. Intentional misuse by deliberately concentrating and inhaling the contents may be harmful or fatal.</p>
    <p><b>California Notice: WARNING!</b> This product contains chemicals known to the State of California to cause cancer, birth defects or other reproductive harm.</p>
    <div class="back__keep">KEEP OUT OF THE REACH OF CHILDREN</div>
    <p><b>For professional use only by trained and qualified paint personnel using all proper safety equipment and application techniques.</b></p>
    <p class="back__contents"><b>Contents:</b> Hexamethylene diisocyanate polymer, butyl acetate, xylene, ethylbenzene, methyl amyl ketone. <b>EMERGENCY TELEPHONE: 1-800-555-0142.</b> Spray rate: 2:1 mix VOC.</p>
    <div class="danger"><span class="danger__word">DANGER</span>
      <svg width="44" height="14" viewBox="0 0 44 14" aria-hidden="true"><g fill="none" stroke="var(--hazard)" stroke-width="1.2"><path d="M7 1l6 6-6 6-6-6z"/><path d="M22 1l6 6-6 6-6-6z"/><path d="M37 1l6 6-6 6-6-6z"/></g><g fill="#111"><circle cx="7" cy="7.5" r="2"/><circle cx="22" cy="7.5" r="2"/><circle cx="37" cy="7.5" r="2"/></g></svg>
    </div>
  </div>
</section>

<!-- ===== MEDIUM ===== -->
<section class="label label--medium">
  <div class="label__texture" role="img" aria-label="Teal dotted wave texture across the navy background"></div>
  <div class="label__spine"><span class="thin">APEX </span><span class="bold">HARDENER</span></div>
  <div class="front">
    <div class="front__texture" role="img" aria-label="Dotted wave texture in deep navy"></div>
    <div class="brand brand--name">VALENCE</div>
    <div class="brand brand--sub">COATINGS</div>
    <div class="product">
      <div class="product__line">APEX</div>
      <div class="product__title">HARDENER<br>FOR CLEAR COAT</div>
      <div class="product__meta"><span>VOC 2.1</span><span class="product__speed">Medium 343</span></div>
    </div>
    <div class="front__size">2.5L</div>
    <div class="front__mix">2:1 MIX</div>
  </div>
  <div class="info">
    <div class="brand brand--name">VALENCE</div>
    <div class="brand brand--sub">COATINGS</div>
    <p class="caps caps--plain">For sale only by professionals.<br>Not for sale to or use by general public</p>
    <p><b>Notice to purchaser:</b> Limited warranty. Seller warrants this product to be free of defects in material and workmanship. Buyer is responsible for determining the suitability of the product for the intended use and assumes all risk and liability in connection with its use.</p>
    <p class="caps">Warning: flammable liquid and vapor. Vapor and spray mist harmful if inhaled. May cause central nervous system effects such as dizziness, headache or nausea. May cause nose, throat, eye and skin irritation. (Follow all directions and cautions on back panel)</p>
    <p><b>Warranty:</b> Recommendations for application are based on tests believed to be reliable. Since conditions of use are beyond our control, no warranty is expressed or implied beyond replacement of product proven defective. Intended for use by professional personnel only.</p>
    <div class="info__address">Valence Coatings, Inc.<br>420 Harbor Park Way,<br>Riverside, CA 92501<br>(888) 555-0147</div>
    <div class="info__origin">Made in EU</div>
    <div class="info__liters">2.5 LITERS</div>
  </div>
  <div class="back">
    <table class="speed-table"><tr><td>Speed</td><td>Temperature</td></tr><tr><td>Slow</td><td>80°F–100°F</td></tr><tr><td>Medium</td><td>65°F–80°F</td></tr><tr><td>Fast</td><td>50°F–65°F</td></tr></table>
    <p><b>Description:</b> Hardener for use with Apex clear coat. Hardener is available in three speeds. Please choose the appropriate speed according to the working temperature.</p>
    <p><b>DIRECTIONS:</b><br>1. Read all label directions, warnings and cautions on panel and hardener.<br>2. Mixing: 2 parts clear coat with 1 part hardener by volume. Stir well.<br>3. Adjust air pressure to 25–30 psi at the gun cap, or 10 psi at the cap for HVLP guns.<br>4. Apply 2 full wet coats, allowing 5–10 minutes flash time between coats for best flow and gloss.<br>5. Dust free in 15 minutes, tack free in 40 minutes at 70°F. May be force dried 30 minutes at 140°F metal temperature after a 10 minute flash.<br>6. Accelerator: up to 1 oz per mixed quart may be added to speed drying in cool conditions. Do not exceed the stated amount or pot life will be shortened.<br>7. Wet sand with 1500 grit or finer and polish after 24 hours air dry or after cool down from bake.<br>8. Clean spray equipment immediately after use with lacquer thinner or gun wash.</p>
    <p><b>WARNING: FLAMMABLE LIQUID AND VAPOR. VAPOR AND SPRAY MIST HARMFUL. MAY CAUSE LUNG IRRITATION AND ALLERGIC RESPIRATORY REACTION.</b> Keep away from heat, sparks and open flame. Vapors may cause flash fire. Persons with asthma or other breathing problems should not use or be exposed to this product. Do not breathe vapors or spray mist. Use only with adequate ventilation. Wear a properly fitted supplied air respirator or an approved organic vapor cartridge respirator during and after application until vapors are gone. Avoid contact with eyes, skin and clothing. Wear chemical resistant gloves and safety glasses. Keep container tightly closed when not in use. Do not reseal if contamination with water is suspected, as pressure may build. Dispose of empty containers and waste according to federal, state and local regulations. Read the Safety Data Sheet before use.</p>
    <p><b>FIRST AID:</b> If inhaled, remove to fresh air and restore breathing if needed; get medical attention. In case of skin contact, wash thoroughly with soap and water and remove contaminated clothing. In case of eye contact, flush with plenty of water for at least 15 minutes and get medical attention. If swallowed, do not induce vomiting; call a physician immediately.</p>
    <p><b>NOTICE:</b> Reports have associated repeated and prolonged occupational overexposure to solvents with permanent brain and nervous system damage. Intentional misuse by deliberately concentrating and inhaling the contents may be harmful or fatal.</p>
    <p><b>California Notice: WARNING!</b> This product contains chemicals known to the State of California to cause cancer, birth defects or other reproductive harm.</p>
    <div class="back__keep">KEEP OUT OF THE REACH OF CHILDREN</div>
    <p><b>For professional use only by trained and qualified paint personnel using all proper safety equipment and application techniques.</b></p>
    <p class="back__contents"><b>Contents:</b> Hexamethylene diisocyanate polymer, butyl acetate, xylene, ethylbenzene, methyl amyl ketone. <b>EMERGENCY TELEPHONE: 1-800-555-0142.</b> Spray rate: 2:1 mix VOC.</p>
    <div class="danger"><span class="danger__word">DANGER</span>
      <svg width="44" height="14" viewBox="0 0 44 14" aria-hidden="true"><g fill="none" stroke="var(--hazard)" stroke-width="1.2"><path d="M7 1l6 6-6 6-6-6z"/><path d="M22 1l6 6-6 6-6-6z"/><path d="M37 1l6 6-6 6-6-6z"/></g><g fill="#111"><circle cx="7" cy="7.5" r="2"/><circle cx="22" cy="7.5" r="2"/><circle cx="37" cy="7.5" r="2"/></g></svg>
    </div>
  </div>
</section>

</body>
</html>
```